IT support company needs Banner Ad for the top of their quote layout template

We need a banner Ad for the top of our for quote layout template so it is sent out on all our quotes

The banner size must be 827 x 100 pixels - anything larger than 60 KB can cause upload time issues

We have attached our logo and examples of the quote page to see how it looks in the context of the whole page.

Essential elements of the banner
- Must have our logo but this can be changed to be different colours if it makes the design work better i.e. Kelmor Wave could be all in white

Colours
- Can use all of our standard colours - Orange, Black, Grey and White

Images
- As a premium IT support company we deal with people and technology so would like to see both of these Incorporated into the banner i.e. people using technology These images could be watermarked or one colour effect.

Look and Feel
- Professional, friendly, people, technology, premium

Target Market
Small business owners and managers

Industry/Entity Type

It Company

```html
<!DOCTYPE html>
<html lang="nl">
<head>
<meta charset="utf-8">
<title>Kelmor Wave – Offerte TR-000280</title>
<link rel="stylesheet" href="https://fonts.googleapis.com/css2?family=Source+Sans+3:wght@400;600;700&display=swap">
<style>
  :root {
    --orange: #f37021;
    --orange-soft: #f5a673;
    --orange-head: #ef8a4c;
    --ink: #1a1a1a;
    --grey-band: #e8e9ea;
    --row-alt: #f1f1f1;
    --backdrop: #d6d6d6;
    --white: #ffffff;
  }
  * { box-sizing: border-box; margin: 0; padding: 0; }
  html, body { width: 965px; height: 1200px; overflow: hidden; }
  body {
    background: var(--backdrop);
    font-family: "Source Sans 3", Arial, sans-serif;
    color: var(--ink);
  }
  .quote-page {
    position: absolute; left: 60px; top: 0;
    width: 833px; height: 1183px;
    background: var(--white);
    transform: scale(1.0144); transform-origin: 0 0;
  }
  .abs { position: absolute; }
  .banner { left: 0; top: 0; width: 833px; height: 111px; }
  .brand-name {
    left: 32px; top: 30px; font-size: 34px; font-weight: 700;
    letter-spacing: 1px; color: var(--ink); text-transform: uppercase;
  }
  .brand-name .dot {
    display: inline-block; width: 12px; height: 12px; background: var(--orange);
    border-radius: 50%; margin-right: 8px; vertical-align: 4px;
  }
  .banner-tagline {
    left: 355px; top: 27px; width: 240px; text-align: center;
    color: var(--white); font-size: 14px; font-weight: 600; line-height: 18px;
    letter-spacing: 0.3px; text-transform: uppercase;
  }
  .doc-title { left: 27px; top: 167px; font-size: 20px; }
  .author-photo {
    left: 25px; top: 205px; width: 100px; height: 133px;
    background: linear-gradient(180deg, #6d6d6d, #3b3b3b);
  }
  .info-block { top: 204px; font-size: 12.5px; line-height: 17px; }
  .info-block h3 { color: var(--orange); font-weight: 400; font-size: 15.5px; margin-bottom: 5px; }
  .info-block b { font-weight: 700; }
  .rule-orange { left: 25px; top: 349px; width: 782px; height: 3px; background: var(--orange); }
  .section-title { left: 27px; font-size: 17.5px; }
  .data-table {
    position: absolute; left: 25px; width: 782px;
    border: 1.5px solid var(--ink); border-collapse: collapse; font-size: 12.5px;
  }
  .data-table th {
    height: 25px; font-weight: 400; text-align: left; padding: 0 5px;
    background: linear-gradient(90deg, var(--orange-head), #fbe3d3 40%, #ffffff 52%, #fbe3d3 64%, var(--orange-head));
  }
  .data-table td { height: 26px; padding: 0 5px; }
  .data-table tbody tr:nth-child(even) td { background: var(--row-alt); }
  .data-table .num { text-align: right; border-left: 1.5px solid var(--ink); }
  .data-table th.num { background: var(--orange-head); }
  .totals { left: 420px; width: 382px; font-size: 12.5px; }
  .totals .line { display: flex; justify-content: flex-end; height: 25px; align-items: center; }
  .totals .label { color: var(--orange); text-align: right; }
  .totals .value { width: 109px; text-align: right; font-weight: 700; }
  .disclaimer { left: 27px; top: 992px; font-size: 12.5px; }
  .sign-line { top: 1066px; height: 1px; background: var(--ink); }
  .sign-label { top: 1068px; font-size: 12.5px; }
  .footer-rule { left: 0; top: 1137px; width: 833px; height: 5px; background: var(--orange-soft); }
  .footer-band {
    left: 0; top: 1142px; width: 833px; height: 41px;
    background: linear-gradient(90deg, #ffffff 5%, #fbdcc7 30%, var(--orange-soft) 52%, #fbdcc7 72%, #ffffff 95%);
    display: flex; justify-content: space-between; align-items: center;
    padding: 0 27px; font-size: 12.5px;
  }
</style>
</head>
<body>
<main class="quote-page">
  <header>
    <svg class="abs banner" viewBox="0 0 833 111" aria-hidden="false">
      <defs>
        <linearGradient id="teamTone" x1="0" x2="1">
          <stop offset="0" stop-color="#6f7378"/>
          <stop offset="1" stop-color="#c9ccd0"/>
        </linearGradient>
      </defs>
      <rect x="0" y="0" width="833" height="100" fill="#e8e9ea"/>
      <rect x="600" y="0" width="233" height="100" fill="url(#teamTone)" role="img" aria-label="Photo of business people working with a laptop and tablet"/>
      <polygon points="378,0 628,0 572,100 298,100" fill="#f37021"/>
      <polygon points="370,0 380,0 302,100 292,100" fill="#1a1a1a"/>
      <polygon points="628,0 638,0 582,100 572,100" fill="#1a1a1a"/>
      <rect x="0" y="104" width="833" height="6" fill="#f5a673"/>
    </svg>
    <div class="abs brand-name"><span class="dot"></span>Kelmor Wave</div>
    <p class="abs banner-tagline">Bringing enterprise-level solutions to East Anglia small businesses</p>
  </header>

  <h1 class="abs doc-title">Standard MSP&nbsp; #2</h1>
  <div class="abs author-photo" role="img" aria-label="Portrait photo of the quote author"></div>

  <section class="abs info-block" style="left:136px">
    <h3>Opgesteld door:</h3>
    <b>Reyner Partners Ltd</b><br>Tomas Reyner<br><br>Fax<br>t.reyner@kelmorwave.example
  </section>
  <section class="abs info-block" style="left:363px">
    <h3>Opgesteld voor:</h3>
    <b>Harlow Finch</b><br>12 Ostler Lane<br>Brindle,&nbsp; 40217<br>Nadia Pell<br>nadia.pell@harlowfinch.example
  </section>
  <section class="abs info-block" style="left:633px">
    <h3>Gegevens Offerte:</h3>
    <b>Offerte #: TR-000280</b><br>Versie: 1<br><div style="height:4px"></div>Leverdatum: 14/11/2017<br>Vervaldatum: 31/12/2017
  </section>
  <div class="abs rule-orange"></div>

  <h2 class="abs section-title" style="top:377px;font-weight:400">Overzicht Offerte</h2>
  <table class="data-table" style="top:406px">
    <thead><tr><th>Beschrijving</th><th class="num" style="width:109px">Bedrag</th></tr></thead>
    <tbody><tr><td style="background:#fff">Initial Investment</td><td class="num" style="background:#fff">$800.00</td></tr></tbody>
  </table>
  <div class="abs totals" style="top:462px">
    <div class="line"><span class="label">Subtotaal:</span><span class="value">$800.00</span></div>
    <div class="line"><span class="label">VAT:</span><span class="value">$160.00</span></div>
    <div class="line"><span class="label">Totaal:</span><span class="value">$960.00</span></div>
  </div>

  <h2 class="abs section-title" style="top:554px;font-weight:400">Overzicht Terugkerende Kosten</h2>
  <table class="data-table" style="top:583px">
    <thead><tr><th>Beschrijving</th><th class="num" style="width:109px">Bedrag</th></tr></thead>
    <tbody>
      <tr><td>Monitoring</td><td class="num">$375.00</td></tr>
      <tr><td>Support</td><td class="num">$65.00</td></tr>
      <tr><td>Fixed Hours</td><td class="num">$850.00</td></tr>
    </tbody>
  </table>
  <div class="abs totals" style="top:691px">
    <div class="line"><span class="label">Terugkerende totaal:</span><span class="value">$1,290.00</span></div>
  </div>

  <h2 class="abs section-title" style="top:747px;font-weight:400">*Optionele kosten</h2>
  <table class="data-table" style="top:775px">
    <thead><tr><th>Beschrijving</th><th class="num" style="width:109px">Recurring</th><th class="num" style="width:109px">One-Time</th></tr></thead>
    <tbody>
      <tr><td>Monitoring</td><td class="num">$790.00</td><td class="num">$0.00</td></tr>
      <tr><td>Support</td><td class="num">$185.00</td><td class="num">$0.00</td></tr>
      <tr><td>Fixed Hours</td><td class="num">$695.00</td><td class="num">$0.00</td></tr>
      <tr><td>Add-on Services</td><td class="num">$850.00</td><td class="num">$0.00</td></tr>
    </tbody>
  </table>
  <div class="abs totals" style="top:910px">
    <div class="line"><span class="label">Optionele terugkerend bedrag:</span><span class="value">$2,520.00</span></div>
    <div class="line"><span class="label">Optionele ongeplande Subtotaal:</span><span class="value">$.00</span></div>
  </div>

  <p class="abs disclaimer">Taxes, shipping, handling and other fees may apply.&nbsp; We reserve the right to cancel orders arising from pricing or other errors.</p>

  <div class="abs sign-line" style="left:25px;width:468px"></div>
  <div class="abs sign-label" style="left:27px">Handtekening</div>
  <div class="abs sign-line" style="left:523px;width:183px"></div>
  <div class="abs sign-label" style="left:525px">Datum</div>

  <div class="abs footer-rule"></div>
  <footer class="abs footer-band"><span>Offerte #TR-000280 v1</span><span>Pagina 6 Van 7</span></footer>
</main>
</body>
</html>
```